Realty Group Needs Classy, Contemporary Letterhead Design

We need a letterhead design for a new realty company located in NY, USA. We buy investment properties to rehabilitate and or keep in our rental portfolio.

```html
<!DOCTYPE html>
<html lang="en">
<head>
<meta charset="utf-8">
<title>Meridian Realty Group — Letterhead</title>
<link href="https://fonts.googleapis.com/css2?family=Montserrat:wght@400;500;600;800&family=Mr+Dafoe&display=swap" rel="stylesheet">
<style>
  :root {
    --backdrop: #e3e3e3;
    --paper: #ffffff;
    --brand-purple: #4e2a84;
    --rail-grey: #7f7f7f;
    --ink: #2e2e2e;
    --ink-dark: #111111;
  }
  * { margin: 0; padding: 0; box-sizing: border-box; }
  html, body {
    width: 1200px; height: 1200px; overflow: hidden;
    background: var(--backdrop);
    font-family: "Montserrat", sans-serif;
  }
  .letterhead {
    position: absolute; left: 198px; top: 30px;
    width: 805px; height: 1140px;
    background: var(--paper);
    box-shadow: 4px 6px 12px rgba(0,0,0,0.25);
    overflow: hidden;
  }
  .side-rail { position: absolute; left: 0; top: 0; width: 21px; height: 1140px; }
  .brand {
    position: absolute; left: 78px; top: 62px;
    color: var(--brand-purple); font-weight: 800; line-height: 1;
  }
  .brand-name { font-size: 50px; letter-spacing: -1px; }
  .brand-tag { font-size: 17px; margin-top: 6px; letter-spacing: 1px; padding-left: 68px; }
  .recipient {
    position: absolute; left: 76px; top: 236px;
    font-size: 14.2px; line-height: 21.6px; color: var(--ink);
  }
  .salutation {
    position: absolute; left: 76px; top: 388px;
    font-size: 14.2px; color: var(--ink);
  }
  .letter-body {
    position: absolute; left: 76px; top: 431px; width: 653px;
    font-size: 14.2px; line-height: 21.6px; color: var(--ink);
    text-align: justify;
  }
  .signature {
    position: absolute; left: 66px; top: 752px;
    font-family: "Mr Dafoe", cursive; font-size: 82px; line-height: 1;
    color: var(--ink-dark);
  }
  .contact-block {
    position: absolute; left: 76px; top: 978px;
    border-left: 2px solid var(--brand-purple);
    padding-left: 9px; height: 118px;
  }
  .contact-address {
    font-size: 11.6px; font-weight: 600; line-height: 14.5px; color: var(--ink-dark);
    margin-bottom: 4px;
  }
  .contact-list { list-style: none; }
  .contact-list li {
    display: flex; align-items: center; gap: 5px;
    font-size: 11.6px; line-height: 17px; color: var(--ink-dark);
  }
  .contact-list svg { width: 9px; height: 9px; flex: none; }
</style>
</head>
<body>
  <main class="letterhead">
    <svg class="side-rail" viewBox="0 0 21 1140" aria-hidden="true">
      <rect x="0" y="0" width="21" height="786" fill="var(--rail-grey)"/>
      <polygon points="0,792 21,804 21,1140 0,1140" fill="var(--brand-purple)"/>
    </svg>

    <header class="brand">
      <div class="brand-name">MERIDIAN</div>
      <div class="brand-tag">Realty Group, LLC</div>
    </header>

    <address class="recipient" style="font-style:normal">
      Mr. John Doe<br>
      President<br>
      Strategy Accountants<br>
      111 Street Name,<br>
      City State, 12345
    </address>

    <p class="salutation">Dear</p>

    <div class="letter-body">
      <p>Lorem ipsum dolor sit amet, consectetur adipiscing elit. Aenean ut ipsum eget massa hendrerit vestibulum vel in velit. Donec pretium neque velit.</p>
      <p>Aliquam porta lectus nec mauris ornare venenatis. Vivamus non est turpis, et cursus sem. Mauris vehicula erat in diam auctor at bibendum nisl lacinia.</p>
      <p>Morbi imperdiet neque vehicula nunc convallis gravida. Vestibulum iaculis pretium placerat. Integer consequat, est sit amet facilisis eleifend, nibh nibh varius orci, eget dapibus arcu dui non purus. Pellentesque in magna mauris. Duis enim sapien, dictum vitae condimentum a, pulvinar vel lacus. Mauris et molestie nibh. Vestibulum vitae nulla at metus elementum porta sit amet interdum elit. Nulla sollicitudin neque eu nulla volutpat congue.</p>
      <p>Etiam pellentesque, velit id dapibus fermentum, turpis sapien ornare dui, ac tincidunt ligula odio congue purus. Nunc sed ante dui, in porta lectus. Cras nec sem lorem. In hac habitasse platea dictumst. Maecenas id diam quis dui porta tristique. Sed id egestas felis. Donec ullamcorper mattis posuere. Phasellus fermentum eleifend tortor vel dapibus. Vestibulum ante ipsum.</p>
    </div>

    <div class="signature">Jonathan Doe</div>

    <footer class="contact-block">
      <div class="contact-address">2150 Harbor View Ave,<br>Suite 001 Albany NY 12207</div>
      <ul class="contact-list">
        <li><svg viewBox="0 0 10 10"><rect x="2.5" y="0.5" width="5" height="9" rx="1" fill="none" stroke="var(--brand-purple)" stroke-width="1"/></svg>555.010.1200</li>
        <li><svg viewBox="0 0 10 10"><path d="M2 1 L4 3 L3 4.5 Q4.5 6.5 5.5 7 L7 6 L9 8 L8 9.5 Q3 9 0.5 2 Z" fill="var(--brand-purple)"/></svg>555.020.1000</li>
        <li><svg viewBox="0 0 10 10"><rect x="0.5" y="2" width="9" height="6.5" fill="var(--brand-purple)"/><path d="M0.5 2 L5 5.5 L9.5 2" fill="none" stroke="#fff" stroke-width="0.8"/></svg>555.030.8046</li>
        <li><svg viewBox="0 0 10 10"><rect x="2.5" y="0.5" width="5" height="3" fill="var(--brand-purple)"/><rect x="0.5" y="3.5" width="9" height="4" rx="1" fill="var(--brand-purple)"/><rect x="2.5" y="6.5" width="5" height="3" fill="var(--brand-purple)" stroke="#fff" stroke-width="0.6"/></svg>jonathan@meridianrealty.com</li>
        <li><svg viewBox="0 0 10 10"><g fill="none" stroke="var(--brand-purple)" stroke-width="0.9"><circle cx="5" cy="5" r="4.3"/><ellipse cx="5" cy="5" rx="1.9" ry="4.3"/><line x1="0.7" y1="5" x2="9.3" y2="5"/></g></svg>www.meridianrealty.com</li>
      </ul>
    </footer>
  </main>
</body>
</html>
```